Lumora Systems New Website - IT Infrastructure | Smart Cabinet | Micro Data Center

We're an IT SI providing Server Room Design & Build | All-in-One Rack & Smart Cabinet | Structured Cabling | IT Relocation | Maintenance. Old website can be found at www.lumorasys.com.hk. We'd like a brand new wix website which is modern, minimalist, interactive with some animation. Website content will be mostly static and include our service, our project, news and events, about us, contacts, blogs, partners and brands, etc.

reference sites:
We'd like to see more designs referring to below

https://www.pixelvane.example/design/41736205
https://www.pixelvane.example/design/41892417
https://velbrinn.example/

Animation (scrolling effect) referring to
https://velbrinn.example/intelligence/smart-office-room/
Updates

we'd like below style.

Designs look the same

Target Market(s)

Commercials in HK

Industry/Entity Type

IT, Technology, Data Center

Coding

Coded - Design and coding required

Font styles to use
Sans Serif

Requirements
Must have
• CMS, Some Interactive Elements/ Graphics

```html
<!DOCTYPE html>
<html lang="en">
<head>
<meta charset="utf-8">
<title>Lumora Systems – IT Infrastructure</title>
<link href="https://fonts.googleapis.com/css2?family=Roboto:wght@400;500;700&display=swap" rel="stylesheet">
<style>
:root{
  --red:#d32f22;
  --red-deep:#a9271d;
  --navy:#0f1a33;
  --ink:#1b1b1b;
  --muted:#666;
  --light:#f2f2f2;
  --white:#fff;
  --footer:#1a1a1a;
}
*{box-sizing:border-box;margin:0;padding:0}
html,body{width:1200px;height:4644px;overflow:hidden}
body{font-family:"Roboto",Arial,sans-serif;color:var(--ink);background:var(--white);position:relative}
.abs{position:absolute}
.btn{position:absolute;background:var(--red);color:#fff;font-weight:500;font-size:15px;display:flex;align-items:center;justify-content:center;gap:5px}
.btn svg{width:16px;height:10px}
.sec-mark{position:absolute;width:5px;height:30px;background:var(--red);display:block}
.sec-title{position:absolute;font-size:34px;font-weight:700;white-space:nowrap}
.sec-title em{font-style:normal;color:var(--red)}
.centered{left:0;width:1200px;display:flex;justify-content:center;align-items:center;gap:16px}
.centered .sec-mark,.centered .sec-title{position:static}

/* header */
.site-header{position:absolute;left:0;top:0;width:1200px;height:85px;background:#fff}
.brand{position:absolute;left:112px;top:25px;display:flex;align-items:center;gap:9px;font-size:25px;font-weight:500;color:var(--navy)}
.brand i{width:26px;height:26px;border:3px solid var(--navy);display:block}
.nav{position:absolute;top:34px;font-size:14px;color:var(--ink)}
.nav.active{color:var(--red)}
.nav-tools{position:absolute;left:852px;top:34px;display:flex;gap:14px}

/* hero */
.hero{position:absolute;left:0;top:85px;width:1200px;height:502px;background:radial-gradient(circle at 80% 40%,#2c3142 0%,#171b26 55%,#0c0e14 100%)}
.hero-people{position:absolute;left:100px;top:85px;width:462px;height:566px;background:linear-gradient(160deg,#6d7280 0%,#4a4f5c 45%,#2a2d36 100%);border-radius:0 0 45% 55% / 0 0 18% 22%}
.hero-copy{position:absolute;left:601px;color:#fff}
.hero-list{position:absolute;left:607px;top:359px;list-style:none;color:#fff;font-size:14px;font-weight:500}
.hero-list li{height:47px;display:flex;align-items:flex-start;gap:14px}
.hero-list li::before{content:"";width:10px;height:10px;background:var(--red);margin-top:3px}

/* about */
.about-frame{position:absolute;left:125px;top:700px;width:388px;height:344px;border:2px solid var(--red)}
.about-photo{position:absolute;left:112px;top:687px;width:381px;height:339px;background:linear-gradient(135deg,#3b414d,#8a8f98 50%,#4f5561)}
.body-text{position:absolute;font-size:13px;line-height:23px;color:var(--muted);text-align:justify}

/* services */
.services{position:absolute;left:0;top:1127px;width:1200px;height:639px;background:var(--light)}
.svc-list{position:absolute;left:112px;top:1478px;list-style:none;font-size:13px;color:#333}
.svc-list li{height:35px;display:flex;gap:9px}
.svc-list svg{width:16px;height:10px;margin-top:4px}
.svc-frame{position:absolute;width:214px;height:215px;border:2px solid var(--red)}
.svc-card{position:absolute;width:214px;height:215px;background:var(--navy);border:2px solid #fff;outline:1px solid var(--navy);color:#fff;display:flex;flex-direction:column;align-items:center;padding-top:40px}
.svc-icon{width:62px;height:62px;background:#fff;display:flex;align-items:center;justify-content:center;margin-bottom:24px}
.svc-card h3{font-size:17px;font-weight:700;text-align:center;line-height:29px}

/* dark band */
.dark-band{position:absolute;left:0;width:1200px;background:linear-gradient(120deg,#0e1830 0%,#17233f 50%,#0b1428 100%)}
.post{position:absolute;width:297px;height:303px;background:#fff}
.post-date{position:absolute;left:0;top:0;width:185px;height:35px;background:#fff;color:var(--red);font-size:16px;font-weight:500;padding-left:42px;line-height:35px;z-index:2}
.post-img{position:absolute;left:0;top:35px;width:297px;height:190px}
.post p{position:absolute;left:14px;top:232px;width:245px;font-size:14.5px;line-height:23px;color:#222}
.post-go{position:absolute;right:6px;bottom:6px;width:26px;height:20px;background:var(--red);display:flex;align-items:center;justify-content:center}
.post-go svg{width:14px;height:9px}
.slide-arrow{position:absolute;width:22px;height:12px}

/* projects */
.proj{position:absolute}
.proj-caption{position:absolute;left:535px;top:2917px;width:553px;text-align:center;font-size:21px;font-weight:500;line-height:33px;color:#222}

/* partners */
.partners{position:absolute;left:0;top:3890px;width:1200px;height:320px;background:var(--red-deep)}
.partner{position:absolute;top:4040px;width:221px;height:103px;background:#fff;display:flex;align-items:center;justify-content:center;gap:10px;font-size:26px;font-weight:700;color:#3a3a3a}
.partner i{width:22px;height:22px;border-radius:50%;background:#3a3a3a;display:block}

/* footer */
.footer{position:absolute;left:0;top:4210px;width:1200px;height:434px;background:var(--footer)}
.f-label{position:absolute;font-size:13px;font-weight:700;color:#fff}
.f-text{position:absolute;font-size:12.5px;line-height:30px;color:#fff}
.social{position:absolute;top:4495px;width:30px;height:30px;border-radius:50%;background:#fff}
.form-box{position:absolute;left:680px;top:4283px;width:408px;height:272px;background:#fff}
.form-head{position:absolute;left:680px;top:4283px;width:408px;height:38px;background:var(--red);color:#fff;font-size:20px;font-weight:700;text-align:center;line-height:38px}
.field{position:absolute;left:694px;width:376px;border:1px solid #bbb;font-size:12px;color:#777;padding:8px 12px}
.copyright{position:absolute;left:0;top:4604px;width:1200px;text-align:center;font-size:11px;color:#ddd}
</style>
</head>
<body>

<svg width="0" height="0" style="position:absolute">
  <defs>
    <symbol id="arrow" viewBox="0 0 16 10"><path d="M0 5h13M9 1l4 4-4 4" stroke="currentColor" stroke-width="1.8" fill="none"/></symbol>
    <symbol id="arrow-left" viewBox="0 0 22 12"><path d="M22 6H3M8 1L2 6l6 5" stroke="currentColor" stroke-width="2" fill="none"/></symbol>
    <symbol id="rack" viewBox="0 0 36 36"><rect x="8" y="3" width="20" height="30" fill="none" stroke="#d32f22" stroke-width="2"/><path d="M11 10h14M11 16h14M11 22h14M11 28h14" stroke="#d32f22" stroke-width="2"/></symbol>
  </defs>
</svg>

<!-- Header -->
<header class="site-header">
  <div class="brand"><i></i>Lumora</div>
  <span class="nav active" style="left:440px">Home</span>
  <svg class="abs" style="left:448px;top:60px" width="16" height="12" viewBox="0 0 16 12"><path d="M2 10h12M4 10V6l4-4 4 4v4" stroke="#d32f22" stroke-width="1.5" fill="none"/></svg>
  <span class="nav" style="left:521px">About</span>
  <span class="nav" style="left:602px">Our Services</span>
  <span class="nav" style="left:728px">Our Projects</span>
  <div class="nav-tools">
    <svg width="14" height="14" viewBox="0 0 14 14"><circle cx="6" cy="6" r="4.5" stroke="#111" stroke-width="2" fill="none"/><path d="M9.5 9.5L13 13" stroke="#111" stroke-width="2"/></svg>
    <svg width="14" height="14" viewBox="0 0 14 14"><circle cx="7" cy="4" r="3" fill="#111"/><path d="M1 14c0-4 3-6 6-6s6 2 6 6z" fill="#111"/></svg>
  </div>
  <div class="btn" style="left:941px;top:25px;width:144px;height:38px;font-size:16px">Contact Us</div>
</header>

<!-- Hero -->
<section class="hero" role="img" aria-label="Dark server room background"></section>
<div class="hero-people" role="img" aria-label="Two IT engineers working on a laptop in a server room"></div>
<p class="hero-copy" style="top:183px;font-size:19px;font-weight:500">Welcome To</p>
<h1 class="hero-copy" style="top:218px;font-size:56px;font-weight:700;letter-spacing:.5px">Lumora Systems</h1>
<p class="hero-copy" style="left:605px;top:317px;font-size:16px;font-weight:500">We're an IT SI providing Server Room Design &amp; Build .</p>
<ul class="hero-list">
  <li>All-in-One Rack &amp; Smart Cabinet</li>
  <li>Structured Cabling</li>
  <li>IT Relocation &amp; Maintenance</li>
</ul>

<!-- About -->
<div class="about-frame"></div>
<div class="about-photo" role="img" aria-label="Engineers discussing in a server aisle"></div>
<span class="sec-mark" style="left:600px;top:675px"></span>
<h2 class="sec-title" style="left:620px;top:668px;font-size:32px">About <em>Us</em></h2>
<p class="body-text" style="left:600px;top:732px;width:473px">Lumora Systems is well experienced in delivering the best in Data Center Infrastructure, Network Infrastructure, Structured Cabling, Telephony, Access Control, Video Surveillance, Audiovisual &amp; Conferencing, Relocation &amp; Migration and Maintenance solutions.</p>
<p class="body-text" style="left:600px;top:843px;width:473px">Our dedication, focus, and expertise wins much recognition of many IT professionals in all industries in the region. In Lumora Systems's belief, the major reason that we gain a lot of true long-lasting business relationship with our clients was that we offer them the attention, consideration, passion, and professionalism that they deserved.</p>
<div class="btn" style="left:600px;top:986px;width:151px;height:42px">View More <svg><use href="#arrow"/></svg></div>

<!-- Services -->
<section class="services"></section>
<span class="sec-mark" style="left:112px;top:1215px"></span>
<h2 class="sec-title" style="left:132px;top:1207px">Our <em>Services</em></h2>
<p class="body-text" style="left:112px;top:1282px;width:390px;color:#333;line-height:23.3px">Lorem ipsum dolor sit amet, consectetur adipiscing elit, sed do eiusmod tempor incididunt ut labore et dolore magna aliqua. Ut enim ad minim veniam, quis nostrud exercitation ullamco laboris nisi ut aliquip ex ea commodo consequat. Duis aute irure dolor in reprehenderit in voluptate velit esse cillum dolore eu fugiat nulla pariatur. Excepteur sint occaecat cupidatat non proident, sunt in culpa qui officia deserunt mollit anim id est laborum.</p>
<ul class="svc-list">
  <li><svg><use href="#arrow"/></svg>Server Room Design &amp; Build</li>
  <li><svg><use href="#arrow"/></svg>All-in-One Rack &amp; Smart Cabinet</li>
  <li><svg><use href="#arrow"/></svg>Structured Cabling</li>
  <li><svg><use href="#arrow"/></svg>IT Relocation</li>
</ul>
<div class="btn" style="left:112px;top:1632px;width:152px;height:42px">View More <svg><use href="#arrow"/></svg></div>

<div class="svc-frame" style="left:605px;top:1232px"></div>
<div class="svc-card" style="left:596px;top:1223px"><div class="svc-icon"><svg width="36" height="36"><use href="#rack"/></svg></div><h3>Data center design<br>and build</h3></div>
<div class="svc-frame" style="left:872px;top:1206px"></div>
<div class="svc-card" style="left:863px;top:1197px"><div class="svc-icon"><svg width="36" height="36"><use href="#rack"/></svg></div><h3>Structured cabling<br>and fiber backbone</h3></div>
<div class="svc-frame" style="left:605px;top:1489px"></div>
<div class="svc-card" style="left:596px;top:1480px"><div class="svc-icon"><svg width="36" height="36"><use href="#rack"/></svg></div><h3>All-In-One Rack /<br>Micro-Data Center</h3></div>
<div class="svc-frame" style="left:872px;top:1464px"></div>
<div class="svc-card" style="left:863px;top:1455px"><div class="svc-icon"><svg width="36" height="36"><use href="#rack"/></svg></div><h3>Audiovisual and<br>Conference Room</h3></div>

<!-- News -->
<section class="dark-band" style="top:1766px;height:622px"></section>
<div class="abs centered" style="top:1836px;color:#fff"><span class="sec-mark"></span><h2 class="sec-title">Our <em>News</em></h2></div>
<svg class="slide-arrow" style="left:60px;top:2071px;color:#fff"><use href="#arrow-left"/></svg>
<svg class="slide-arrow" style="left:1114px;top:2071px;color:#fff;transform:scaleX(-1)"><use href="#arrow-left"/></svg>
<article class="post" style="left:112px;top:1935px"><span class="post-date">Dec 20,2023</span><div class="post-img" role="img" aria-label="Technician working on a server rack" style="background:linear-gradient(135deg,#2f3540,#6b707a)"></div><p>Lorem ipsum dolor sit amet, consectetur adipiscing elit, sed do eiusmod tempor i</p><span class="post-go"><svg style="color:#fff"><use href="#arrow"/></svg></span></article>
<article class="post" style="left:449px;top:1935px"><span class="post-date">Dec 20,2023</span><div class="post-img" role="img" aria-label="Long data center aisle" style="background:linear-gradient(180deg,#1c2a3c,#5e7a98 60%,#9aa9b8)"></div><p>Lorem ipsum dolor sit amet, consectetur adipiscing elit, sed do eiusmod tempor i</p><span class="post-go"><svg style="color:#fff"><use href="#arrow"/></svg></span></article>
<article class="post" style="left:788px;top:1935px"><span class="post-date">Dec 20,2023</span><div class="post-img" role="img" aria-label="Engineer inspecting server equipment" style="background:linear-gradient(135deg,#c9ccd0,#7b8088 55%,#3d4048)"></div><p>Lorem ipsum dolor sit amet, consectetur adipiscing elit, sed do eiusmod tempor i</p><span class="post-go"><svg style="color:#fff"><use href="#arrow"/></svg></span></article>
<div class="btn" style="left:524px;top:2271px;width:152px;height:41px">View More <svg><use href="#arrow"/></svg></div>

<!-- Projects -->
<div class="abs centered" style="top:2471px;color:var(--ink)"><span class="sec-mark"></span><h2 class="sec-title">Our <em>Projects</em></h2></div>
<div class="proj" role="img" aria-label="Blue patch cables in a rack" style="left:112px;top:2558px;width:410px;height:357px;background:linear-gradient(90deg,#1d4c86,#4a86c8 40%,#234f85 70%,#8e9298)"></div>
<div class="proj" role="img" aria-label="Black server cabinets" style="left:112px;top:2928px;width:410px;height:237px;background:linear-gradient(135deg,#e8e8e8,#3a3b3e 40%,#1d1e20 80%)"></div>
<div class="proj" role="img" aria-label="Patch panel with blue cables" style="left:535px;top:2558px;width:553px;height:246px;background:linear-gradient(180deg,#1e3f6c,#3f79bd 50%,#1f2530)"></div>
<div class="proj" role="img" aria-label="Finished server room for a securities firm" style="left:535px;top:2817px;width:553px;height:348px;background:linear-gradient(135deg,#dcdcdc,#cfcfcf 50%,#e3e3e3)"></div>
<p class="proj-caption">A RENOWNED CHINA BASED<br>SECURITIES FIRM</p>
<div class="btn" style="left:748px;top:2997px;width:150px;height:40px">View More <svg><use href="#arrow"/></svg></div>

<!-- Events -->
<section class="dark-band" style="top:3274px;height:616px"></section>
<div class="abs centered" style="top:3343px;color:#fff"><span class="sec-mark"></span><h2 class="sec-title">Our Events</h2></div>
<svg class="slide-arrow" style="left:60px;top:3578px;color:#fff"><use href="#arrow-left"/></svg>
<svg class="slide-arrow" style="left:1114px;top:3578px;color:#fff;transform:scaleX(-1)"><use href="#arrow-left"/></svg>
<article class="post" style="left:112px;top:3443px"><span class="post-date">Dec 20,2023</span><div class="post-img" role="img" aria-label="Training session in a computer room" style="background:linear-gradient(180deg,#eef0f2,#9ea3aa 60%,#3d4046)"></div><p>Lorem ipsum dolor sit amet, consectetur adipiscing elit, sed do eiusmod tempor i</p><span class="post-go"><svg style="color:#fff"><use href="#arrow"/></svg></span></article>
<article class="post" style="left:449px;top:3443px"><span class="post-date">Dec 20,2023</span><div class="post-img" role="img" aria-label="Speaker presenting to a conference audience" style="background:linear-gradient(180deg,#3a2c2a,#8a4a32 50%,#2a1f22)"></div><p>Lorem ipsum dolor sit amet, consectetur adipiscing elit, sed do eiusmod tempor i</p><span class="post-go"><svg style="color:#fff"><use href="#arrow"/></svg></span></article>
<article class="post" style="left:788px;top:3443px"><span class="post-date">Dec 20,2023</span><div class="post-img" role="img" aria-label="Team gathering in an office" style="background:linear-gradient(135deg,#c9c6c0,#7a6f62 50%,#3f4a3a)"></div><p>Lorem ipsum dolor sit amet, consectetur adipiscing elit, sed do eiusmod tempor i</p><span class="post-go"><svg style="color:#fff"><use href="#arrow"/></svg></span></article>
<div class="btn" style="left:524px;top:3779px;width:152px;height:41px">View More <svg><use href="#arrow"/></svg></div>

<!-- Partners -->
<section class="partners"></section>
<div class="abs centered" style="top:3944px;color:#fff"><span class="sec-mark" style="background:#fff"></span><h2 class="sec-title" style="font-size:32px">Our Partners</h2></div>
<svg class="slide-arrow" style="left:60px;top:4085px;color:#fff"><use href="#arrow-left"/></svg>
<svg class="slide-arrow" style="left:1114px;top:4085px;color:#fff;transform:scaleX(-1)"><use href="#arrow-left"/></svg>
<div class="partner" style="left:112px"><i></i>NORVALE</div>
<div class="partner" style="left:363px">KESTRIN</div>
<div class="partner" style="left:614px">Ardemo</div>
<div class="partner" style="left:865px">Quillon</div>

<!-- Footer -->
<footer class="footer"></footer>
<div class="brand" style="top:4286px;color:#fff"><i style="border-color:#fff"></i>Lumora</div>
<span class="f-label" style="left:113px;top:4369px">Address</span>
<p class="f-text" style="left:113px;top:4395px">Rm 1208, 12/F, Harbourline Centre,<br>18 Kwai Fong Road,<br>Kwai Chung, Hong Kong</p>
<span class="f-label" style="left:393px;top:4369px">Email:</span>
<p class="f-text" style="left:393px;top:4390px">marketing@lumorasys.com.hk</p>
<span class="f-label" style="left:393px;top:4437px">Phone</span>
<p class="f-text" style="left:393px;top:4463px">+852 2480 6100 / +852 5930 4718</p>
<span class="social" style="left:114px" aria-label="Social link"></span>
<span class="social" style="left:161px" aria-label="Messaging link"></span>

<div class="form-box"></div>
<div class="form-head">Get In Touch</div>
<div class="field" style="top:4343px;height:33px">Name</div>
<div class="field" style="top:4388px;height:33px">Email</div>
<div class="field" style="top:4433px;height:58px">Message</div>
<div class="btn" style="left:805px;top:4518px;width:150px;height:39px;font-size:16px">Submit</div>
<p class="copyright">© 2023 by LumoraSys. All Rights Reserved</p>

</body>
</html>
```